Business card design for Automotive workshop

We need a business card for a new automotive repair and tyre shop called Keelstone Prime Automotive located in New Zealand. We are a clean, modern and fresh workshop and company.

Front needs to feature logo,
my name:
Marlo Fenwicke (director)

Address:
48 Tarn Lane
Whitianga 3510

Phone: 07 594 2713
Mobile: 027 451 9362
Email: office@keelstoneautomotive.example.nz
Website: keelstoneautomotive.example.nz

Back needs to feature an area to write down appointment details, date and time.

Also feature a list of jobs and work we do such as,
Vehicle Servicing
All Mechanical Repairs
Warrant of Fitness
Tyres & Wheel Alignments
Automotive Diagnostics
Automotive Parts & Supplies

```html
<!DOCTYPE html>
<html lang="en">
<head>
<meta charset="utf-8">
<title>Keelstone Prime Automotive – Business Card</title>
<link rel="stylesheet" href="https://fonts.googleapis.com/css2?family=Arimo:wght@400&display=swap">
<style>
  :root {
    --backdrop: #717275;
    --card-black: #030303;
    --brand-red: #e42328;
    --text-red: #e8262b;
  }
  * { box-sizing: border-box; margin: 0; padding: 0; }
  html, body {
    width: 1200px;
    height: 965px;
    overflow: hidden;
    background: var(--backdrop);
    font-family: "Arimo", Arial, sans-serif;
  }
  .sheet {
    position: relative;
    width: 1200px;
    height: 965px;
  }
  .card {
    position: absolute;
    left: 281px;
    width: 639px;
    height: 373px;
    border-radius: 29px;
    overflow: hidden;
    background: var(--card-black);
    box-shadow: 0 3px 8px rgba(0, 0, 0, 0.35);
  }
  .card--back { top: 74px; }
  .card--front { top: 518px; }

  .edge-band {
    position: absolute;
    top: 0;
    bottom: 0;
    background: var(--brand-red);
  }
  .edge-band--left { left: 0; width: 29px; }
  .edge-band--right { right: 0; width: 14px; }

  .service-list { list-style: none; }
  .service-item,
  .booking-field {
    position: absolute;
    left: 35px;
    display: flex;
    align-items: center;
    color: var(--text-red);
    font-size: 16.5px;
    letter-spacing: 0.3px;
    word-spacing: 4px;
    white-space: nowrap;
    transform: translateY(-50%);
  }
  .bullet {
    display: inline-block;
    width: 8px;
    height: 8px;
    border-radius: 50%;
    background: var(--text-red);
    margin-right: 4px;
    flex: none;
  }
  .service-item--indented .bullet { margin-right: 11px; }
  .booking-field .bullet { margin-right: 8px; }
  .write-line {
    position: absolute;
    left: 94px;
    width: 216px;
    height: 3px;
    background: var(--text-red);
  }

  .brand-name {
    position: absolute;
    left: 349px;
    top: 166px;
    width: 250px;
    color: var(--brand-red);
    text-align: center;
    line-height: 1;
    font-weight: 400;
    white-space: nowrap;
  }
  .brand-name__main {
    display: block;
    font-size: 29px;
    letter-spacing: 6.5px;
    margin-right: -6.5px;
  }
  .brand-name__sub {
    display: block;
    margin-top: 6px;
    font-size: 11.5px;
    letter-spacing: 4.2px;
    margin-right: -4.2px;
  }

  .holder {
    position: absolute;
    left: 44px;
    top: 62px;
    color: var(--text-red);
  }
  .holder__name {
    font-size: 21px;
    letter-spacing: 0.5px;
    line-height: 1;
  }
  .holder__role {
    margin-top: 6px;
    font-size: 13px;
    letter-spacing: 2px;
    line-height: 1;
  }
  .contact-list { list-style: none; }
  .contact-item {
    position: absolute;
    left: 35px;
    display: flex;
    align-items: center;
    color: var(--text-red);
    font-size: 14.5px;
    letter-spacing: 0.2px;
    white-space: nowrap;
    transform: translateY(-50%);
  }
  .contact-item .bullet { margin-right: 9px; }
  .contact-item--plain { padding-left: 17px; }
  .contact-label { display: inline-block; width: 58px; }
</style>
</head>
<body>
<main class="sheet">

  <section class="card card--back" aria-label="Appointment card, back">
    <div class="edge-band edge-band--left"></div>
    <div class="edge-band edge-band--right"></div>

    <ul class="service-list">
      <li class="service-item" style="top:104px"><span class="bullet"></span>Vehicle Servicing</li>
      <li class="service-item" style="top:130px"><span class="bullet"></span>All Mechanical Repairs</li>
      <li class="service-item" style="top:159px"><span class="bullet"></span>Warrant of Fitness</li>
      <li class="service-item service-item--indented" style="top:184px"><span class="bullet"></span>Tyres &amp; Wheel Alignments</li>
      <li class="service-item service-item--indented" style="top:212px"><span class="bullet"></span>Automotive Parts &amp; Supplies</li>
      <li class="service-item service-item--indented" style="top:240px"><span class="bullet"></span>Automotive Diagnostics</li>
    </ul>

    <div class="booking-field" style="top:300px"><span class="bullet"></span>Date</div>
    <div class="write-line" style="top:302px"></div>
    <div class="booking-field" style="top:331px"><span class="bullet"></span>Time</div>
    <div class="write-line" style="top:336px"></div>

    <p class="brand-name">
      <span class="brand-name__main">KEELSTONE</span>
      <span class="brand-name__sub">PRIME AUTOMOTIVE</span>
    </p>
  </section>

  <section class="card card--front" aria-label="Business card, front">
    <div class="edge-band edge-band--left"></div>
    <div class="edge-band edge-band--right"></div>

    <div class="holder">
      <p class="holder__name">Marlo Fenwicke</p>
      <p class="holder__role">DIRECTOR</p>
    </div>

    <ul class="contact-list">
      <li class="contact-item" style="top:150px"><span class="bullet"></span>48 Tarn Lane</li>
      <li class="contact-item contact-item--plain" style="top:172px">Whitianga 3510</li>
      <li class="contact-item" style="top:208px"><span class="bullet"></span><span class="contact-label">Phone</span>07 594 2713</li>
      <li class="contact-item" style="top:234px"><span class="bullet"></span><span class="contact-label">Mobile</span>027 451 9362</li>
      <li class="contact-item" style="top:270px"><span class="bullet"></span>office@keelstoneautomotive.example.nz</li>
      <li class="contact-item" style="top:296px"><span class="bullet"></span>keelstoneautomotive.example.nz</li>
    </ul>

    <p class="brand-name">
      <span class="brand-name__main">KEELSTONE</span>
      <span class="brand-name__sub">PRIME AUTOMOTIVE</span>
    </p>
  </section>

</main>
</body>
</html>
```